Wired Earphone Creative Packaging Design

We would like a creative window box style packaging design for our wired earphone

Size: 6” x 3.5” x 1.5” (enclosed die-cut drawing)
Material: E Flute Paper box
Type: Window Box style
Design features we prefer: friendly, playful, creative, trendy, unique, High tech.
Competitors: Enclosed
Requirement:AI file is preferred

Enclosed are product pictures, marketing materials and competitor designs for your reference.

Any further questions, please feel free to ask.
Updates

So designers get more time to design

Target Market(s)

13-40 Year Olds

Industry/Entity Type

Audio

Colors

Designer to choose colors to be used in the design.

Requirements
Must have
• Window, selling point, creative

```html
<!DOCTYPE html>
<html lang="en">
<head>
<meta charset="utf-8">
<title>Stereo In-Ear Earphones – Window Box Dieline</title>
<link href="https://fonts.googleapis.com/css2?family=Montserrat:wght@600;700&display=swap" rel="stylesheet">
<style>
  :root {
    --sun-yellow: #e9d23e;
    --charcoal: #353535;
    --ink: #1a1a1a;
    --window-white: #ffffff;
    --fold-blue: #2d4fa8;
    --cut-line: #111111;
    --bleed-line: #e0cf3a;
  }
  html, body {
    margin: 0;
    padding: 0;
    width: 1200px;
    height: 1200px;
    overflow: hidden;
    background: var(--charcoal);
  }
  .dieline-canvas {
    display: block;
    width: 1200px;
    height: 1200px;
    font-family: "Montserrat", Arial, sans-serif;
  }
  .bg-top { fill: var(--sun-yellow); }
  .bg-bottom { fill: var(--charcoal); }
  .cut { fill: none; stroke: var(--cut-line); stroke-width: 1.2; }
  .fold { fill: none; stroke: var(--fold-blue); stroke-width: 1; stroke-dasharray: 5 4; }
  .bleed { stroke: var(--bleed-line); stroke-width: 1; }
  .window { fill: var(--window-white); stroke: var(--cut-line); stroke-width: 1.2; }
  .info-text { fill: var(--ink); font-weight: 600; font-size: 11.5px; text-anchor: middle; }
  .title-main { fill: var(--ink); font-weight: 700; font-size: 22px; letter-spacing: 0.3px; }
  .title-lid { fill: var(--ink); font-weight: 700; font-size: 17px; letter-spacing: 0.3px; }
  .model-tag-bg { fill: var(--charcoal); }
  .model-tag { fill: var(--sun-yellow); font-weight: 600; }
  .features-head { fill: var(--sun-yellow); font-weight: 700; font-size: 18px; text-anchor: middle; }
  .features-text { fill: var(--sun-yellow); font-weight: 600; font-size: 11.5px; text-anchor: middle; }
  .product-photo { fill: url(#earbudTone); }
  .controller-photo { fill: url(#controllerTone); }
</style>
</head>
<body>
<svg class="dieline-canvas" viewBox="0 0 1200 1200" xmlns="http://www.w3.org/2000/svg">
  <defs>
    <linearGradient id="earbudTone" x1="0" y1="0" x2="1" y2="1">
      <stop offset="0" stop-color="#f4f4f4"/>
      <stop offset="0.6" stop-color="#e8e8e8"/>
      <stop offset="1" stop-color="#f0b640"/>
    </linearGradient>
    <linearGradient id="controllerTone" x1="0" y1="0" x2="1" y2="0">
      <stop offset="0" stop-color="#f2f2f2"/>
      <stop offset="0.8" stop-color="#e6e6e6"/>
      <stop offset="1" stop-color="#e8c53a"/>
    </linearGradient>
  </defs>

  <!-- background bands -->
  <rect class="bg-top" x="0" y="0" width="1200" height="566"/>
  <rect class="bg-bottom" x="0" y="566" width="1200" height="634"/>

  <!-- bleed marks -->
  <line class="bleed" x1="0" y1="16" x2="1200" y2="16"/>
  <line class="bleed" x1="29" y1="884" x2="29" y2="1200"/>
  <line class="bleed" x1="0" y1="1106" x2="596" y2="1106"/>

  <!-- cut lines: top flaps -->
  <g class="cut">
    <path d="M29 244 V244 M32 244 V92 H403 V244"/>
    <rect x="107" y="156" width="221" height="17" rx="8.5"/>
    <path d="M94 244 V252 M342 244 V252"/>
    <path d="M406 244 V108 Q406 94 420 94 H483 V158 Q483 166 491 166 Q497 166 497 158 V94 H546 Q560 94 560 108 V232 L566 244"/>
    <path d="M570 244 V84 H634 V40 Q634 16 658 16 H858 Q882 16 882 40 V84 H946 V232 L946 244"/>
    <rect x="648" y="154" width="221" height="17" rx="8.5"/>
    <path d="M952 244 L957 232 V108 Q957 94 971 94 H1036 V158 Q1036 166 1044 166 Q1050 166 1050 158 V94 H1087 Q1101 94 1101 108 V232 L1109 244"/>
  </g>

  <!-- cut lines: body and glue tab -->
  <g class="cut">
    <path d="M29 244 V878 H408"/>
    <path d="M1109 244 L1194 258 V864 L1109 878"/>
  </g>

  <!-- cut lines: bottom flaps -->
  <g class="cut">
    <path d="M408 878 L412 886 L428 1030 H560 V886 L570 878"/>
    <path d="M570 882 V1042 H607 V1034 M574 1042 V1082 Q574 1106 598 1106 H920 Q944 1106 944 1082 V1042 M946 882 V1042 H908 V1034"/>
    <path d="M948 878 L957 890 V1030 H1089 L1105 886 L1109 878"/>
  </g>

  <!-- fold lines -->
  <g class="fold">
    <line x1="29" y1="244" x2="1109" y2="244"/>
    <line x1="408" y1="878" x2="1109" y2="878"/>
    <line x1="634" y1="84" x2="882" y2="84"/>
    <line x1="408" y1="244" x2="408" y2="878"/>
    <line x1="569" y1="244" x2="569" y2="878"/>
    <line x1="948" y1="244" x2="948" y2="878"/>
    <line x1="1109" y1="244" x2="1109" y2="878"/>
    <line x1="607" y1="1042" x2="908" y2="1042"/>
  </g>

  <!-- product imagery placeholders -->
  <rect class="product-photo" role="img" aria-label="Product photo: white earbud with orange cap and black silicone tip" x="584" y="100" width="100" height="82" rx="30"/>
  <rect class="controller-photo" role="img" aria-label="Product photo: in-line mic controller and cord" x="818" y="150" width="110" height="80" rx="14"/>
  <rect class="product-photo" role="img" aria-label="Product photo: pair of white earbuds with orange caps and black tips" x="408" y="252" width="146" height="242" rx="40"/>
  <rect class="controller-photo" role="img" aria-label="Product photo: white in-line remote control with yellow side buttons" x="1002" y="580" width="98" height="248" rx="6"/>

  <!-- window cut-out -->
  <rect class="window" x="526" y="328" width="464" height="467" rx="14"/>

  <!-- left side panel info -->
  <g class="info-text">
    <text x="214" y="285">Earbuds, Controller, Jack, 4 Customizable caps</text>
    <text x="214" y="314">Contents</text>
    <text x="214" y="328">2 Pairs of Switchable Caps</text>
    <text x="214" y="343">3 Pairs of Silicone Ear tips</text>
    <text x="214" y="357">User Manual</text>
    <text x="214" y="386">Specification:</text>
    <text x="214" y="415">Frequency Response: 20-20KHz</text>
    <text x="214" y="429">Sensitivity: 105±3dB</text>
    <text x="214" y="443">THD: &lt;3%</text>
    <text x="214" y="458">Cord Length: 3.6ft</text>
  </g>

  <!-- front panel title -->
  <text class="title-main" x="584" y="272">CUSTOMIZABLE STEREO</text>
  <text class="title-main" x="584" y="299">IN- EAR EARPHONES</text>
  <rect class="model-tag-bg" x="586" y="305" width="133" height="14"/>
  <text class="model-tag" x="590" y="317" font-size="11.5">Model Number: SC-1</text>

  <!-- lid title -->
  <text class="title-lid" x="713" y="104">CUSTOMIZABLE STEREO</text>
  <text class="title-lid" x="713" y="125">IN- EAR EARPHONES</text>
  <rect class="model-tag-bg" x="714" y="130" width="104" height="11"/>
  <text class="model-tag" x="718" y="139" font-size="8.5">Model Number: SC-1</text>

  <!-- features -->
  <text class="features-head" x="758" y="823">Features:</text>
  <text class="features-text" x="758" y="838">Customizable earbuds | In Line Mic | Silicone Gel Ear tips</text>
  <text class="features-text" x="758" y="852">3.5mm Jack | Ergonomic Design</text>
</svg>
</body>
</html>
```